Redgum Ridge Towing website

We need a website design for a towing company based in Australia.
The design should be simple and minimalist. The site can be in colours of the logo are Blue, Red and White (see attached) - but we'd like to see options in some sort of industrial looking metallic theme if possible.
We base our business on our friendly and efficient customer service, the design should attempt to convey this in some way.

```html
<!DOCTYPE html>
<html lang="en">
<head>
<meta charset="utf-8">
<title>Redgum Ridge Towing</title>
<link href="https://fonts.googleapis.com/css2?family=Open+Sans:wght@400;600;700&display=swap" rel="stylesheet">
<style>
:root{
  --navy:#0e1b3d;
  --navy-deep:#081229;
  --navy-panel:#13275a;
  --red:#d3191f;
  --red-dark:#a80f14;
  --white:#ffffff;
  --ink:#333333;
  --muted:#666666;
  --steel:#3a4150;
}
*{margin:0;padding:0;box-sizing:border-box}
html,body{width:853px;height:1200px;overflow:hidden}
body{font-family:"Open Sans",Arial,sans-serif;background:var(--white);color:var(--ink);position:relative}
.site-header{position:absolute;left:0;top:0;width:853px;height:80px;background:linear-gradient(180deg,#1c2232 0%,#0b0f19 100%)}
.brand{position:absolute;left:22px;top:10px;display:flex;align-items:center;gap:8px}
.brand-dot{width:14px;height:14px;border-radius:50%;background:var(--red)}
.brand-name{color:var(--white);font-weight:700;font-size:15px;letter-spacing:.3px}
.call-now{position:absolute;right:22px;top:12px;color:var(--white);font-size:10px;font-weight:700}
.call-now span{font-weight:400;margin-left:4px}
.main-nav{position:absolute;left:313px;right:0;top:40px;height:28px;background:linear-gradient(180deg,#e32027,var(--red-dark));display:flex;align-items:center;justify-content:flex-end;padding-right:18px;gap:26px}
.main-nav a{color:var(--white);text-decoration:none;font-size:10px;font-weight:700;text-transform:uppercase}
.hero{position:absolute;left:85px;top:90px;width:683px;height:320px;background:linear-gradient(180deg,#cfd6dd 0%,#9aa4ad 55%,#5d6b4c 100%)}
.hero-dots{position:absolute;left:50%;bottom:10px;transform:translateX(-50%);display:flex;gap:6px}
.hero-dots i{width:7px;height:7px;border-radius:50%;background:var(--white);opacity:.6}
.hero-dots i.on{opacity:1}
.welcome{position:absolute;left:85px;top:436px;width:450px}
.welcome h1{font-size:19px;font-weight:400;color:var(--navy);margin-bottom:14px}
.welcome p{font-size:9px;line-height:14px;color:var(--muted);margin-bottom:12px}
.contact-box{position:absolute;left:556px;top:436px;width:212px;height:196px;background:var(--navy-panel);padding:10px 12px}
.contact-box h2{color:var(--white);font-size:15px;font-weight:400;margin-bottom:8px;border-bottom:1px solid #2d4583;padding-bottom:6px}
.field{height:18px;border-bottom:1px solid #2d4583;color:#c9d1e6;font-size:8px;padding-top:4px;margin-bottom:4px}
.field.tall{height:30px}
.submit{display:inline-block;margin-top:8px;background:var(--red);color:var(--white);font-size:8px;font-weight:700;padding:5px 12px}
.services-title{position:absolute;left:0;width:853px;top:752px;text-align:center;color:var(--navy);font-size:17px;font-weight:400}
.services{position:absolute;left:85px;top:786px;width:683px;display:flex;gap:14px}
.service{width:160px}
.service-photo{height:100px;margin-bottom:6px}
.service h3{font-size:9.5px;font-weight:700;color:var(--ink);margin-bottom:3px}
.service p{font-size:8px;line-height:11px;color:var(--muted);margin-bottom:7px}
.read-more{display:inline-block;background:var(--red);color:var(--white);font-size:8px;font-weight:700;padding:4px 8px}
.site-footer{position:absolute;left:0;top:1048px;width:853px;height:120px;background:var(--navy);display:flex;padding:12px 85px 0;gap:24px}
.foot-col{flex:1}
.foot-col h4{color:var(--white);font-size:11px;font-weight:600;margin-bottom:6px}
.foot-col li{list-style:none;color:#c3cbe0;font-size:7.5px;line-height:11px}
.foot-col p{color:#c3cbe0;font-size:7.5px;line-height:10px;margin-bottom:4px}
.input{height:13px;background:var(--white);color:#888;font-size:7px;padding:2px 4px;margin-bottom:3px;width:120px}
.subscribe{display:inline-block;background:var(--red);color:var(--white);font-size:7.5px;font-weight:700;padding:2px 8px}
.social li{display:flex;align-items:center;justify-content:flex-end;gap:6px;margin-bottom:6px}
.social-dot{width:13px;height:13px;border-radius:50%;background:#3c5aa6}
.copyright{position:absolute;left:0;top:1168px;width:853px;height:32px;background:var(--navy-deep);color:#aab3cc;font-size:8px;text-align:center;line-height:32px}
</style>
</head>
<body>
<header class="site-header">
  <div class="brand"><span class="brand-dot"></span><span class="brand-name">Redgum Ridge Towing</span></div>
  <div class="call-now">CALL NOW <span>1-300-555-0199</span></div>
  <nav class="main-nav">
    <a href="#">Home</a><a href="#">About Us</a><a href="#">Towing Services</a><a href="#">Get a Quote</a><a href="#">Contact Us</a>
  </nav>
</header>

<section class="hero" role="img" aria-label="Tow truck carrying a silver SUV on its flatbed along a tree-lined road">
  <div class="hero-dots"><i class="on"></i><i></i><i></i></div>
</section>

<section class="welcome">
  <h1>Welcome to Redgum Ridge Towing</h1>
  <p>Redgum Ridge Towing has been moving stranded cars, vans and trucks across the region for more than twenty years. Our drivers are local, friendly and trained to get you and your vehicle somewhere safe quickly. Whether it is a flat battery on a quiet country road or a breakdown in peak hour city traffic, one call brings a truck to you with honest, upfront pricing and no hidden fees. We know how stressful a breakdown can be, so our team keeps you informed from the moment you call until your vehicle is dropped off. Every operator carries the right gear for the job, and every truck is cleaned, checked and serviced regularly so it is always ready to roll when you need it most.</p>
  <p>We run a modern fleet of tilt trays, heavy tow trucks and low loaders, ready day and night, every day of the year. Every job is handled with care, from a short trip to the local workshop to a long haul interstate move. Our dispatch team answers every call in person and sends the nearest available truck straight to your location. We work with insurers, dealers, fleet owners and roadside clubs, and we are happy to quote for one-off jobs or regular contracts. Tell us where you are and where you need to go, and we will take care of the rest, so you can get back on the road without stress and with a smile.</p>
</section>

<aside class="contact-box">
  <h2>Contact US</h2>
  <div class="field">Name</div>
  <div class="field">E-mail</div>
  <div class="field">Phone</div>
  <div class="field tall">Message</div>
  <span class="submit">SUBMIT</span>
</aside>

<h2 class="services-title">Our Services</h2>
<section class="services">
  <article class="service">
    <div class="service-photo" role="img" aria-label="Tilt tray truck carrying a car" style="background:linear-gradient(180deg,#9fb3c6,#5a6570)"></div>
    <h3>Tilt Tray</h3>
    <p>Safe tilt tray transport for cars, bikes and small machinery, loaded gently and delivered where you need them. Our trays suit low cars, prestige vehicles and project cars, and every load is strapped and checked before we leave.</p>
    <span class="read-more">Read More</span>
  </article>
  <article class="service">
    <div class="service-photo" role="img" aria-label="Heavy tow truck on the road" style="background:linear-gradient(180deg,#b8c4cf,#7a3a3a)"></div>
    <h3>Heavy Towing</h3>
    <p>Large trucks, buses and plant moved by experienced operators with heavy rated equipment and careful planning. We cover highways and remote roads, day or night, and keep you updated until the job is complete.</p>
    <span class="read-more">Read More</span>
  </article>
  <article class="service">
    <div class="service-photo" role="img" aria-label="Recovery truck lifting a vehicle" style="background:linear-gradient(180deg,#c7d0d8,#4b5a6a)"></div>
    <h3>Recovery Specialist</h3>
    <p>Accident and off road recovery handled quickly, with winching and lifting gear for even the toughest jobs. Our crews work safely around traffic and terrain, and clear the scene so everyone can move on fast.</p>
    <span class="read-more">Read More</span>
  </article>
  <article class="service">
    <div class="service-photo" role="img" aria-label="Semi trailer tow truck parked in a yard" style="background:linear-gradient(180deg,#a9b9c9,#8a2b2b)"></div>
    <h3>Semi Tilts Low Loaders</h3>
    <p>Semi tilt and low loader hire for machinery, containers and oversized loads across the state and beyond. We help with permits, escorts and route planning so large moves run smoothly and arrive on time.</p>
    <span class="read-more">Read More</span>
  </article>
</section>

<footer class="site-footer">
  <div class="foot-col">
    <h4>Quick Links</h4>
    <ul><li>Home</li><li>About Us</li><li>Services</li><li>Service Plans</li><li>News</li><li>FAQ &amp; Wiki</li><li>Contact Us</li></ul>
  </div>
  <div class="foot-col">
    <h4>Support Links</h4>
    <ul><li>Legal Notice</li><li>Privacy Policy</li><li>Terms &amp; Conditions</li><li>Help</li></ul>
  </div>
  <div class="foot-col">
    <h4>Newsletter SignUp</h4>
    <p>Sign up for our news emails by entering your information below.</p>
    <div class="input">Name</div>
    <div class="input">Enter your E-Mail ID</div>
    <span class="subscribe">Subscribe</span>
  </div>
  <div class="foot-col">
    <h4 style="text-align:right">Connect With Us</h4>
    <ul class="social">
      <li><span>Chirper</span><span class="social-dot"></span></li>
      <li><span>Friendbook</span><span class="social-dot"></span></li>
      <li><span>Worklink</span><span class="social-dot"></span></li>
    </ul>
  </div>
</footer>
<div class="copyright">Copyright ©2013 Company Name - All rights reserved.</div>
</body>
</html>
```